Dental office stationary (letterhead, envelopes), business cards, presentation folders

Nothing too dental outside of the logo. I will need all stationary, presentation folders, business cards. Would prefer to stay in the colors of the logo

Gordon Patel, DDS
Bright Haven Dental Implant Center
555-318-2790
info@brighthavendental.example
4817 NW Maple Crest Rd Unit B
Stuart, FL 00000

Also need appointment date and time
And cancellation policy
I want it to say “kindly ask for
A 48hr cancellation policy to avoid incurring a cancellation fee”

Industry/Entity Type

Dental

Colors
0054AA
0677BA
7BADD7
CADEEF
E8F1F8

Requirements
Must have
• Name of your office, name of doctor, address, phone number
Should not have
• Too much tooth/dental. Only the tooth in logo

```html
<!DOCTYPE html>
<html lang="en">
<head>
<meta charset="utf-8">
<title>Bright Haven Dental Implant Center – Business Card</title>
<link href="https://fonts.googleapis.com/css2?family=Roboto:wght@400;500;700&display=swap" rel="stylesheet">
<style>
  :root {
    --canvas-bg: #2a2c30;
    --card-white: #ffffff;
    --sky: #1bc3ef;
    --blue-mid: #0e8fd6;
    --blue-deep: #0e6bbd;
    --teal: #17b99c;
    --name-blue: #12a3e3;
    --text-grey: #4a4d52;
    --divider: #555a60;
  }
  * { margin: 0; padding: 0; box-sizing: border-box; }
  html, body { width: 1200px; height: 900px; overflow: hidden; }
  body {
    background: var(--canvas-bg);
    font-family: "Roboto", Arial, sans-serif;
    display: flex;
    flex-direction: column;
    align-items: center;
    justify-content: center;
    gap: 40px;
  }
  .card {
    position: relative;
    width: 640px;
    height: 366px;
    overflow: hidden;
    box-shadow: 0 12px 30px rgba(0,0,0,.45);
  }

  /* Front */
  .card-front { background: var(--card-white); }
  .stripe { position: absolute; }
  .stripe-sky { left: 0; top: 112px; width: 200px; height: 10px; background: var(--sky); }
  .stripe-deep { right: 0; top: 112px; width: 170px; height: 10px; background: var(--blue-deep); }
  .stripe-teal { left: 0; top: 126px; width: 640px; height: 3px; background: var(--teal); }
  .brand-front {
    position: absolute;
    left: 212px; top: 76px;
    display: flex; align-items: center; gap: 8px;
    color: var(--teal);
    font-weight: 500;
    font-size: 34px;
    letter-spacing: 3px;
    text-transform: uppercase;
  }
  .brand-dot { width: 14px; height: 14px; border-radius: 50%; background: currentColor; }
  .identity { position: absolute; left: 40px; top: 168px; text-align: right; width: 250px; }
  .doctor-name { color: var(--name-blue); font-weight: 700; font-size: 19px; }
  .practice-name { color: var(--text-grey); font-size: 13.5px; margin-top: 4px; }
  .divider { position: absolute; left: 306px; top: 166px; width: 1px; height: 62px; background: var(--divider); }
  .contacts { position: absolute; left: 322px; top: 164px; list-style: none; }
  .contacts li { display: flex; align-items: center; gap: 8px; font-size: 14px; color: var(--text-grey); line-height: 22px; }
  .contacts svg { width: 13px; height: 13px; fill: var(--teal); flex: none; }
  .web-domain { color: var(--teal); }
  .address { position: absolute; left: 40px; top: 282px; font-size: 14px; color: var(--text-grey); }

  /* Back */
  .card-back { background: var(--teal); }
  .back-art { position: absolute; inset: 0; }
  .brand-back {
    position: absolute;
    left: 0; right: 0; top: 150px;
    display: flex; justify-content: center; align-items: center; gap: 10px;
    color: var(--card-white);
    font-weight: 500;
    font-size: 40px;
    letter-spacing: 4px;
    text-transform: uppercase;
  }
  .brand-back .brand-dot { width: 16px; height: 16px; }
</style>
</head>
<body>

  <section class="card card-front" aria-label="Business card front">
    <div class="stripe stripe-sky"></div>
    <div class="stripe stripe-deep"></div>
    <div class="stripe stripe-teal"></div>
    <div class="brand-front"><span class="brand-dot"></span>Bright Haven</div>

    <div class="identity">
      <p class="doctor-name">Gordon Patel, DDS</p>
      <p class="practice-name">Bright Haven Dental Implant Center</p>
    </div>
    <div class="divider"></div>
    <ul class="contacts">
      <li><svg viewBox="0 0 16 16"><path d="M3 1h3l1.5 4-2 1.2a9 9 0 0 0 4.3 4.3L11 8.5l4 1.5v3a2 2 0 0 1-2 2A12 12 0 0 1 1 3a2 2 0 0 1 2-2z"/></svg>555-318-2790</li>
      <li><svg viewBox="0 0 16 16"><path d="M1 3h14v10H1z M2 4.5v.3l6 4 6-4v-.3z" fill-rule="evenodd"/></svg>info@brighthavendental.example</li>
      <li><svg viewBox="0 0 16 16"><circle cx="8" cy="8" r="7"/></svg>www.<span class="web-domain">brighthavendental</span>.example</li>
    </ul>
    <p class="address">4817 NW Maple Crest Rd Unit B, Stuart, FL 00000</p>
  </section>

  <section class="card card-back" aria-label="Business card back">
    <svg class="back-art" viewBox="0 0 640 366" preserveAspectRatio="none">
      <defs>
        <linearGradient id="backBlue" x1="0" y1="0" x2="1" y2="1">
          <stop offset="0" stop-color="#1bc3ef"/>
          <stop offset="1" stop-color="#0e6bbd"/>
        </linearGradient>
      </defs>
      <path d="M0 0 H300 C470 40 590 160 640 300 V366 H0 Z" fill="url(#backBlue)"/>
      <path d="M270 10 C440 44 570 150 622 290" fill="none" stroke="#ffffff" stroke-width="5" stroke-linecap="round"/>
    </svg>
    <div class="brand-back"><span class="brand-dot"></span>Bright Haven</div>
  </section>

</body>
</html>
```